Webdesign für Bilderbücher für Kinder
Zielgruppe
Wir sind ein Verlag für zweisprachige Bilderbücher für Kinder im Alter von 2-8 Jahren. Wir suchen ein Design für eine mit SHOPIFY neu zu erstellende Website, über die die Bücher verkauft werden sollen.
Der Verlag ist das deutsche Imprint eines internationalen Autoren (zur Orientierung siehe www.tarowinkelbooks.com oder bit.ly/tarowinkel).
Da das Thema sehr bunt ist und mit der Sprachen-Niche noch nicht prominent besetzt ist, wollen wir hier bewusst NICHT so viele Vorgaben machen, was das Design angeht.
Aufgabenstellung
Logo und Beispiele aus bestehenden Büchern sind als Attachments angehängt.
Beispielseiten zur Orientierung, die uns gefallen, sind die folgenden:
https://www.tarowinkelbooks.com/
https://www.edition-mopalu.com/
Ein gutes Design hat der Wolkenhopp Verlag
https://www.wolkenhoppverlag.de/
oder der Pavilo Verlag
https://shop.pavilo-verlag.de/

```html
<!DOCTYPE html>
<html lang="de">
<head>
<meta charset="utf-8">
<title>Bunte Wiese Verlag – Hop, little frog</title>
<link href="https://fonts.googleapis.com/css2?family=Dosis:wght@300;400;500;600;700&display=swap" rel="stylesheet">
<style>
:root{
  --bg-top:#7aa2d9;
  --bg-mid:#a7c4ea;
  --white:#ffffff;
  --ink:#2f3340;
  --muted:#6d7280;
  --light:#9aa0ab;
  --red:#c8242d;
  --green:#7fae1c;
  --star:#f6c14a;
  --line:#e7e8ec;
  --grey-band:#f3f3f4;
  --sky-band:#c9e9f6;
  --navy:#3b6b9a;
  --link:#4a7db3;
  --tag-green:#a5de8e;
  --tag-blue:#8fb8ea;
  --tag-red:#f18d8d;
  --tag-violet:#cfa2ef;
  --tag-olive:#d9c86a;
  --tag-mint:#7fdba8;
}
*{box-sizing:border-box;margin:0;padding:0}
html,body{width:1200px;height:2242px;overflow:hidden}
body{
  font-family:"Dosis",sans-serif;color:var(--ink);
  background:linear-gradient(180deg,var(--bg-top) 0%,var(--bg-mid) 55%,var(--bg-top) 100%);
  position:relative;
}
.page{position:absolute;left:120px;top:77px;width:960px;height:2081px;background:var(--white);overflow:hidden}
.page::before,.page::after{content:"";position:absolute;left:0;right:0;height:3px;
  background:repeating-linear-gradient(90deg,var(--red) 0 60px,transparent 60px 130px,var(--red) 130px 150px,transparent 150px 210px)}
.page::before{top:0}.page::after{bottom:0}
.abs{position:absolute}

/* header */
.header{left:0;top:0;width:960px;height:102px;box-shadow:0 6px 14px rgba(0,0,0,.04)}
.brand{left:78px;top:36px;display:flex;align-items:center;gap:8px}
.brand-dot{width:14px;height:14px;border-radius:50%;background:var(--red)}
.brand-name{font-size:19px;font-weight:500;color:var(--navy);letter-spacing:.5px}
.nav{left:270px;top:47px;display:flex;gap:22px;font-size:12.5px;font-weight:400;color:var(--muted)}
.nav span{position:relative}
.nav .active{color:var(--ink)}
.nav .active::after{content:"";position:absolute;left:-6px;right:-6px;bottom:-6px;height:2px;background:var(--red)}
.icon{width:16px;height:16px}
.badge{position:absolute;top:-7px;right:-8px;width:13px;height:13px;border-radius:50%;font-size:8px;color:#fff;display:flex;align-items:center;justify-content:center;font-weight:600}
.user{left:757px;top:40px;display:flex;align-items:center;gap:7px}
.avatar{width:30px;height:30px;border-radius:4px;background:linear-gradient(135deg,#e9c9b0,#5a4038)}
.user small{display:block;font-size:6.5px;color:var(--light)}
.user b{font-size:11.5px;font-weight:600;color:var(--navy)}

/* gallery */
.frame{background:#fff;box-shadow:0 2px 8px rgba(0,0,0,.08);padding:8px}
.frame div{width:100%;height:100%}

/* product */
.stars{display:flex;gap:3px;align-items:center}
.stars i{width:10px;height:10px;background:var(--star);clip-path:polygon(50% 0,61% 35%,98% 35%,68% 57%,79% 91%,50% 70%,21% 91%,32% 57%,2% 35%,39% 35%)}
.rating{left:500px;top:165px;font-size:11px;color:var(--muted)}
.title{left:500px;top:191px;font-size:17px;font-weight:500;white-space:nowrap}
.author{left:500px;top:218px;font-size:9px;color:var(--ink)}
.author a{color:var(--link);text-decoration:none}
.rule{height:1px;background:var(--line)}
.h-small{font-size:12px;font-weight:500}
.desc{left:500px;top:281px;width:372px;font-size:7.6px;line-height:13px;color:var(--muted);font-family:"Dosis",sans-serif}
.desc p{margin-bottom:13px}
.desc b{color:var(--ink);font-weight:600}
.price{left:500px;top:548px;font-size:25px;color:var(--green);font-weight:400;display:flex;align-items:center;gap:6px}
.price small{font-size:6px;line-height:7px;color:var(--green)}
.flag{width:16px;height:16px;border-radius:50%;overflow:hidden;display:inline-block}
.qty{left:500px;top:596px;width:96px;height:29px;border:1px solid var(--line);display:flex;justify-content:space-between;align-items:center;padding:0 10px;font-size:11px;color:var(--muted)}
.cart-btn{left:600px;top:596px;width:129px;height:29px;background:var(--red);color:#fff;font-size:9px;font-weight:600;display:flex;align-items:center;justify-content:center;gap:14px;border-radius:2px}
.wish{left:735px;top:596px;width:30px;height:29px;border:1px solid var(--line);display:flex;align-items:center;justify-content:center}
.spec{display:flex;gap:9px}
.spec svg{width:18px;height:18px;flex:none;margin-top:1px}
.spec b{display:block;font-size:10px;font-weight:500}
.spec span{font-size:8px;color:var(--muted)}
.tag{position:absolute;height:20px;padding:0 10px;border-radius:2px;color:#fff;font-size:9px;display:flex;align-items:center}

/* reviews */
.reviews{left:0;top:1000px;width:960px;height:396px;background:var(--grey-band)}
.sec-title{font-size:24px;font-weight:300;color:var(--ink);text-align:center;width:960px;left:0}
.review{top:92px;width:258px;height:210px;background:#fff;box-shadow:0 2px 8px rgba(0,0,0,.06);padding:20px 18px}
.review h4{font-size:8.5px;font-weight:700;margin:14px 0 8px}
.review p{font-size:7.6px;line-height:18px;color:var(--muted)}
.review em{display:block;margin-top:7px;font-size:8px;color:var(--ink)}
.btn-red{background:var(--red);color:#fff;font-size:9px;font-weight:600;display:flex;align-items:center;justify-content:center;border-radius:2px}

/* recommendations */
.rec{top:1479px;width:120px}
.rec .cover{height:122px;background:#fff;box-shadow:0 2px 8px rgba(0,0,0,.08);padding:6px}
.rec .cover div{width:100%;height:100%}
.rec .by{margin-top:12px;font-size:7px;color:var(--link)}
.rec .name{font-size:9.5px;white-space:nowrap;overflow:hidden;text-overflow:ellipsis;margin-top:2px}
.rec .row{display:flex;gap:4px;margin-top:6px}
.rec .pr{height:18px;padding:0 7px;background:var(--green);color:#fff;font-size:9px;display:flex;align-items:center;border-radius:1px}
.rec .hw{width:18px;height:18px;border:1px solid var(--line);display:flex;align-items:center;justify-content:center}

/* newsletter */
.news{left:0;top:1705px;width:960px;height:183px;background:var(--sky-band)}
.news h3{position:absolute;left:148px;top:64px;font-size:27px;font-weight:500;color:var(--navy);line-height:26px}
.news h3 span{display:block;font-weight:300;font-size:22px}
.news .input{position:absolute;left:486px;top:75px;width:313px;height:33px;background:#fff;font-size:9px;color:var(--ink);display:flex;align-items:center;padding-left:16px}
.news .submit{position:absolute;left:799px;top:75px;width:80px;height:33px}

/* footer */
.foot-text{left:78px;top:1969px;width:340px;font-size:7.6px;line-height:14px;color:var(--muted)}
.social{left:78px;top:2030px;display:flex;gap:24px}
.social i{width:13px;height:13px;border-radius:50%;background:var(--navy)}
.foot-links{left:485px;top:1936px}
.foot-links h5{font-size:12px;font-weight:500;margin-bottom:16px}
.foot-links li{list-style:none;font-size:8px;line-height:14px;color:var(--ink);position:relative;padding-left:10px}
.foot-links li::before{content:"";position:absolute;left:0;top:5px;width:4px;height:4px;border-radius:50%;background:var(--red)}
</style>
</head>
<body>
<main class="page">

  <header class="abs header">
    <div class="abs brand"><span class="brand-dot"></span><span class="brand-name">Bunte Wiese Verlag</span></div>
    <nav class="abs nav">
      <span>Start</span><span class="active">Bücher</span><span>Verlag</span><span>Kitas /Schulen</span><span>Blog</span><span>Kontakt</span>
    </nav>
    <svg class="abs icon" style="left:645px;top:47px" viewBox="0 0 16 16" fill="none" stroke="#2f3340" stroke-width="1.6"><circle cx="7" cy="7" r="5"/><path d="M11 11l4 4"/></svg>
    <div class="abs" style="left:680px;top:47px">
      <svg class="icon" viewBox="0 0 16 16" fill="none" stroke="#2f3340" stroke-width="1.4"><path d="M8 14S2 10 2 5.8A3 3 0 0 1 8 4a3 3 0 0 1 6 1.8C14 10 8 14 8 14z"/></svg>
      <span class="badge" style="background:#f0a81e">21</span>
    </div>
    <div class="abs" style="left:717px;top:47px">
      <svg class="icon" viewBox="0 0 16 16" fill="none" stroke="#2f3340" stroke-width="1.4"><path d="M1 2h2l2 8h8l2-6H4"/><circle cx="6" cy="13.5" r="1"/><circle cx="12" cy="13.5" r="1"/></svg>
      <span class="badge" style="background:var(--red)">5</span>
    </div>
    <div class="abs user"><div class="avatar" role="img" aria-label="Profilfoto der Nutzerin"></div><div><small>Willkommen zurück!</small><b>Lena</b></div></div>
    <svg class="abs" style="left:870px;top:52px" width="9" height="6" viewBox="0 0 9 6" fill="none" stroke="#6d7280" stroke-width="1.2"><path d="M1 1l3.5 3.5L8 1"/></svg>
  </header>

  <!-- gallery -->
  <div class="abs frame" style="left:78px;top:149px;width:393px;height:393px"><div role="img" aria-label="Buchcover: Aquarell mit Vögeln auf einem Ast vor grüner Wiese" style="background:linear-gradient(180deg,#cfe7ef 0%,#b7d98c 45%,#8fc25a 85%,#f6c583 100%)"></div></div>
  <div class="abs frame" style="left:78px;top:567px;width:190px;height:190px"><div role="img" aria-label="Innenseite mit Vögeln auf einem Baum" style="background:linear-gradient(180deg,#c7e2ee,#9ccf6e)"></div></div>
  <div class="abs frame" style="left:283px;top:567px;width:190px;height:190px"><div role="img" aria-label="Innenseite mit fliegenden Vögeln und Text" style="background:linear-gradient(180deg,#c3e1f1,#a9d27b 60%,#eef1d6)"></div></div>
  <div class="abs frame" style="left:78px;top:772px;width:190px;height:190px"><div role="img" aria-label="Innenseite mit kleinem Vogel allein" style="background:radial-gradient(circle at 55% 45%,#fbf8ef 30%,#dbe9c7 75%,#f2c9b8)"></div></div>
  <div class="abs frame" style="left:283px;top:772px;width:190px;height:190px"><div role="img" aria-label="Titelseite des Buches" style="background:#fbefd9"></div></div>

  <!-- product info -->
  <div class="abs stars rating"><i></i><i></i><i></i><i></i><i></i><span style="margin-left:6px">5.0</span></div>
  <h1 class="abs title" style="font-weight:500">Hop, little frog - Hüpf, kleiner Frosch (English/German)</h1>
  <div class="abs author">Autor: <a>Taro Winkel</a></div>
  <div class="abs rule" style="left:500px;top:241px;width:372px"></div>
  <h2 class="abs h-small" style="left:500px;top:257px">Beschreibung</h2>
  <div class="abs desc">
    <p>Der kleine Frosch liebt den Teich. Er versucht zu springen, kann aber nie mehr als ein paar Zentimeter hochhüpfen. Er hat zu viel Angst. Also sieht er zu, wie die anderen Frösche über die Seerosen hüpfen und ihn verlassen. Doch dann passiert etwas Seltsames… Lesen Sie, wie der schüchterne kleine Frosch seine Ängste überwindet.</p>
    <p>Das Besondere an diesem Buch:</p>
    <p>• <b>Jede Zeile ist sowohl in Englisch als auch in Deutsch</b><br>• Die Geschichte ist einfach und für das Lernen im frühen Alter geeignet<br>• Führt Konzepte der Problemlösung, Zusammenarbeit und Teamarbeit ein.<br>• <b>Alle Illustrationen sind originell, kreativ und super lustig</b><br>• Außerdem gibt es am Ende des Buches EXTRA-SEITEN zum Ausmalen und Zeichnen<br>• <b>UND SO VIEL MEHR!</b></p>
    <p>Kinder lernen schnell und einfach. Mit zweisprachigen Kinderbüchern verhelfen Sie ihnen schon früh zum Erfolg und erweitern ihren Horizont! Diese zweisprachige Geschichte wurde speziell entwickelt, um Kindern beim Vorlesen neue Fremdwörter und Redewendungen beizubringen. Das Buch ist auch in anderen Sprachen erhältlich.</p>
    <p>Für alle Kinder, die Englisch oder Deutsch als Zweitsprache lernen.</p>
  </div>
  <div class="abs price">24,90 € <small>inkl. MwSt.<br>und Versand</small>
    <span style="margin-left:22px;display:flex;gap:6px">
      <svg class="flag" viewBox="0 0 16 16"><rect width="16" height="5.4" fill="#111"/><rect y="5.3" width="16" height="5.4" fill="#d8202a"/><rect y="10.6" width="16" height="5.4" fill="#f5c518"/></svg>
      <svg class="flag" viewBox="0 0 16 16"><rect width="16" height="16" fill="#1f3f8f"/><path d="M0 0L16 16M16 0L0 16" stroke="#fff" stroke-width="3"/><path d="M8 0v16M0 8h16" stroke="#fff" stroke-width="4"/><path d="M8 0v16M0 8h16" stroke="#d8202a" stroke-width="2"/></svg>
    </span>
  </div>
  <div class="abs qty"><span>−</span><span style="color:var(--ink)">2</span><span>+</span></div>
  <div class="abs cart-btn">in die Büchertruhe
    <svg width="16" height="14" viewBox="0 0 16 14" fill="none" stroke="#fff" stroke-width="1.2"><rect x="2" y="5" width="12" height="8" rx="1"/><path d="M2 8h12M4 5c0-3 8-3 8 0"/></svg>
  </div>
  <div class="abs wish"><svg width="13" height="12" viewBox="0 0 16 16" fill="none" stroke="#b4b8c0" stroke-width="1.4"><path d="M8 14S2 10 2 5.8A3 3 0 0 1 8 4a3 3 0 0 1 6 1.8C14 10 8 14 8 14z"/></svg></div>
  <div class="abs rule" style="left:500px;top:646px;width:372px"></div>

  <div class="abs spec" style="left:500px;top:676px"><svg viewBox="0 0 18 18" fill="none" stroke="#8a8f99"><rect x="2" y="3" width="14" height="13"/><path d="M2 7h14M6 1v4M12 1v4"/></svg><div><b>Erscheinungsdatum</b><span>29. März 2021</span></div></div>
  <div class="abs spec" style="left:643px;top:676px"><svg viewBox="0 0 18 18" fill="none" stroke="#8a8f99"><path d="M3 4l8-2 4 11-8 3z"/><path d="M5 7l6-1"/></svg><div><b>Seitenanzahl</b><span>52</span></div></div>
  <div class="abs spec" style="left:776px;top:676px"><svg viewBox="0 0 18 18" fill="none" stroke="#8a8f99"><path d="M2 2h5v14H2zM7 4l8 10"/><path d="M4 5h2M4 8h2M4 11h2"/></svg><div><b>Größe</b><span>21,59 x 21,59 cm</span></div></div>
  <div class="abs spec" style="left:500px;top:718px"><svg viewBox="0 0 18 18" fill="none" stroke="#8a8f99"><path d="M2 10l10-5 4 3-10 5z"/><path d="M5 9l2 2M8 8l2 2"/></svg><div><b>ISBN</b><span>9781234509876</span></div></div>
  <div class="abs spec" style="left:643px;top:718px"><svg viewBox="0 0 18 18" fill="none" stroke="#8a8f99"><path d="M3 16V6l3-4 3 4v10zM11 16V8h4v8"/></svg><div><b>Illustrator</b><span>Mila Korsak</span></div></div>
  <div class="abs spec" style="left:776px;top:718px"><svg viewBox="0 0 18 18" fill="none" stroke="#8a8f99"><path d="M2 14l3-9 3 9M3 11h4M10 5v9M10 9c4-2 4 5 0 5"/></svg><div><b>Übersetzer</b><span>Greta Lindner</span></div></div>
  <div class="abs spec" style="left:500px;top:764px"><svg viewBox="0 0 18 18" fill="none" stroke="#8a8f99"><circle cx="9" cy="8" r="5"/><path d="M4 17c0-4 10-4 10 0"/></svg><div><b>Lesealter</b><span>ab 4 Jahren</span></div></div>
  <div class="abs rule" style="left:500px;top:814px;width:372px"></div>

  <h2 class="abs h-small" style="left:500px;top:832px;font-size:10.5px">Kategorien</h2>
  <span class="tag" style="left:501px;top:866px;background:var(--tag-green)">Comic</span>
  <span class="tag" style="left:560px;top:866px;background:var(--tag-blue)">Kinderbücher</span>
  <span class="tag" style="left:636px;top:866px;background:var(--tag-red)">Kinder ab 4</span>
  <span class="tag" style="left:704px;top:866px;background:var(--tag-violet)">Englische Bücher</span>
  <span class="tag" style="left:501px;top:893px;background:var(--tag-olive);width:88px;justify-content:center">Mehrsprachig</span>
  <span class="tag" style="left:596px;top:893px;background:var(--tag-mint)">Lernbücher</span>

  <!-- reviews -->
  <section class="abs reviews">
    <h2 class="abs sec-title" style="top:32px">
      <svg width="16" height="18" viewBox="0 0 16 18" fill="none" stroke="#8a8f99" style="vertical-align:-2px;margin-right:6px"><path d="M4 2h8v5a4 4 0 0 1-8 0zM4 4H1c0 3 2 4 3 4M12 4h3c0 3-2 4-3 4M8 11v4M5 17h6"/></svg>Kundenrezensionen</h2>
    <article class="abs review" style="left:78px"><div class="stars"><i></i><i></i><i></i><i></i><i></i></div><h4>Immer wieder!</h4><p>Ein Buch, das Sehnsüchte weckt und zum Träumen einlädt. Ein Buch, dass einem längst vergessene Orte zeigt und Plätze, die man sich in den kühnsten Abenteuern nicht vorstellen konnte. Ein Buch vom Meer, von Inseln, die unwirtlich sind, die die Könige waren, um dann wieder in der Versenkung zu verschwinden. Einfach super!</p><em>Lena am 14/03/20</em></article>
    <article class="abs review" style="left:351px"><div class="stars"><i></i><i></i><i></i><i></i><i></i></div><h4>Immer wieder!</h4><p>Ein Buch, das Sehnsüchte weckt und zum Träumen einlädt. Ein Buch, dass einem längst vergessene Orte zeigt und Plätze, die man sich in den kühnsten Abenteuern nicht vorstellen konnte. Ein Buch vom Meer, von Inseln, die unwirtlich sind, die die Könige waren, um dann wieder in der Versenkung zu verschwinden. Einfach super!</p><em>Lena am 14/03/20</em></article>
    <article class="abs review" style="left:624px"><div class="stars"><i></i><i></i><i></i><i></i><i></i></div><h4>Immer wieder!</h4><p>Ein Buch, das Sehnsüchte weckt und zum Träumen einlädt. Ein Buch, dass einem längst vergessene Orte zeigt und Plätze, die man sich in den kühnsten Abenteuern nicht vorstellen konnte. Ein Buch vom Meer, von Inseln, die unwirtlich sind, die die Könige waren, um dann wieder in der Versenkung zu verschwinden. Einfach super!</p><em>Lena am 14/03/20</em></article>
    <div class="abs btn-red" style="left:429px;top:332px;width:99px;height:30px">mehr anzeigen</div>
  </section>

  <!-- recommendations -->
  <h2 class="abs sec-title" style="top:1426px">Unsere Empfehlung</h2>
  <div class="abs rec" style="left:78px"><div class="cover"><div role="img" aria-label="Buchcover mit Baum unter blauem Himmel" style="background:linear-gradient(180deg,#bfe0f1,#7fb7d8 60%,#9ccf6e)"></div></div><div class="by">Taro Winkel</div><div class="name">Der tanzende Mond</div><div class="row"><span class="pr">€ 24.90</span><span class="hw"><svg width="10" height="9" viewBox="0 0 16 16" fill="none" stroke="#b4b8c0" stroke-width="1.6"><path d="M8 14S2 10 2 5.8A3 3 0 0 1 8 4a3 3 0 0 1 6 1.8C14 10 8 14 8 14z"/></svg></span></div></div>
  <div class="abs rec" style="left:215px"><div class="cover"><div role="img" aria-label="Buchcover mit Tier auf Wiese" style="background:linear-gradient(180deg,#e8f2f7,#c7e2ee 60%,#9ccf6e)"></div></div><div class="by">Taro Winkel</div><div class="name">Hüpf, kleiner Frosch</div><div class="row"><span class="pr">€ 14.90</span><span class="hw"><svg width="10" height="9" viewBox="0 0 16 16" fill="none" stroke="#b4b8c0" stroke-width="1.6"><path d="M8 14S2 10 2 5.8A3 3 0 0 1 8 4a3 3 0 0 1 6 1.8C14 10 8 14 8 14z"/></svg></span></div></div>
  <div class="abs rec" style="left:351px"><div class="cover"><div role="img" aria-label="Buchcover mit Figuren auf einem Fahrrad" style="background:linear-gradient(180deg,#fbe7c8,#f4b77a 70%,#e0603a)"></div></div><div class="by">Taro Winkel</div><div class="name">Be brave! - Sei mutig!</div><div class="row"><span class="pr">€ 9.90</span><span class="hw" style="background:#f0a81e;border-color:#f0a81e"><svg width="10" height="9" viewBox="0 0 16 16" fill="none" stroke="#fff" stroke-width="1.6"><path d="M8 14S2 10 2 5.8A3 3 0 0 1 8 4a3 3 0 0 1 6 1.8C14 10 8 14 8 14z"/></svg></span></div></div>
  <div class="abs rec" style="left:487px"><div class="cover"><div role="img" aria-label="Buchcover mit Tieren am Fluss" style="background:linear-gradient(180deg,#e4f1f6,#8fc1d3 50%,#a3c96a)"></div></div><div class="by">Taro Winkel</div><div class="name">Freunde am Teich - Das ung…</div><div class="row"><span class="pr">€ 24.90</span><span class="hw"><svg width="10" height="9" viewBox="0 0 16 16" fill="none" stroke="#b4b8c0" stroke-width="1.6"><path d="M8 14S2 10 2 5.8A3 3 0 0 1 8 4a3 3 0 0 1 6 1.8C14 10 8 14 8 14z"/></svg></span></div></div>
  <div class="abs rec" style="left:624px"><div class="cover"><div role="img" aria-label="Buchcover mit bunter Zirkusszene" style="background:linear-gradient(180deg,#8b2e6e,#e24a4a 50%,#f5d033)"></div></div><div class="by">Taro Winkel</div><div class="name">Pip The Ant - Pip die Ameise</div><div class="row"><span class="pr">€ 10.90</span><span class="hw"><svg width="10" height="9" viewBox="0 0 16 16" fill="none" stroke="#b4b8c0" stroke-width="1.6"><path d="M8 14S2 10 2 5.8A3 3 0 0 1 8 4a3 3 0 0 1 6 1.8C14 10 8 14 8 14z"/></svg></span></div></div>
  <div class="abs rec" style="left:760px"><div class="cover"><div role="img" aria-label="Buchcover mit zwei Kindern auf einer Bank" style="background:linear-gradient(180deg,#bfe3f6,#8cc8ea 60%,#6aa6d8)"></div></div><div class="by">Taro Winkel</div><div class="name">Plant A Tree! It's The Only…</div><div class="row"><span class="pr">€ 24.90</span><span class="hw"><svg width="10" height="9" viewBox="0 0 16 16" fill="none" stroke="#b4b8c0" stroke-width="1.6"><path d="M8 14S2 10 2 5.8A3 3 0 0 1 8 4a3 3 0 0 1 6 1.8C14 10 8 14 8 14z"/></svg></span></div></div>

  <!-- newsletter -->
  <section class="abs news">
    <h3>Abonniere unseren Newsletter<span>und verpasse keine Neuigkeiten</span></h3>
    <div class="input">Trage deine E-Mail-Adresse ein</div>
    <div class="submit btn-red">Abonnieren</div>
  </section>

  <!-- footer -->
  <div class="abs brand" style="top:1920px"><span class="brand-dot" style="width:11px;height:11px"></span><span class="brand-name" style="font-size:15px">Bunte Wiese Verlag</span></div>
  <p class="abs foot-text">Eine wunderbare Heiterkeit hat meine ganze Seele eingenommen, gleich den süßen Frühlingsmorgen, die ich mit ganzem Herzen genieße. Ich bin allein und freue mich meines Lebens in dieser Gegend, die für solche Seelen geschaffen ist wie die meine.</p>
  <div class="abs social" aria-label="Soziale Netzwerke"><i></i><i></i><i></i><i></i></div>
  <div class="abs foot-links">
    <h5>Noch eine Kleinigkeit...</h5>
    <ul><li>Datenschutz</li><li>AGB</li><li>Kontakt</li><li>Wir in der Presse</li></ul>
  </div>
  <div class="abs" role="img" aria-label="Illustration: Großvater und Kind auf einem Fahrrad" style="left:628px;top:1907px;width:240px;height:174px;background:radial-gradient(ellipse at 30% 45%,#f2783a 0 28%,transparent 29%),radial-gradient(ellipse at 68% 55%,#d9cbb8 0 34%,transparent 35%)"></div>
</main>
</body>
</html>
```